Need a developer to develop and design my virtual employee recruitment solution website.

I need the entire website developed, from the design, the navigation, the contents of the website, etc. I need a professional looking website yet have that modern look. You can suggest the best fonts, color combinations to use. I need the site to be SEO friendly. I also want high quality stock photos to be used on the website. I wanted to achieve a similar website like this https://remotehelperpool.example/.

Target Market(s)

Ecommerce Entrepreneurs, Businessmen, Cartwell and Bazorra Sellers.

Industry/Entity Type

Professional Service

Coding

Coded - Design and coding required

Number of Pages Required

5+ page

Font styles to use
Sans Serif

Requirements
Must have
• I wanted it to have pages like this https://remotehelperpool.example/
Nice to have
• open for any recommendation you can suggest
Should not have
• Cannot think of any. You can suggest your own here

```html
<!DOCTYPE html>
<html lang="en">
<head>
<meta charset="utf-8">
<title>RemoteHarbor — Virtual Employee Recruitment</title>
<link rel="stylesheet" href="https://fonts.googleapis.com/css2?family=Montserrat:wght@500;600;700&family=Open+Sans:wght@400;600&display=swap">
<style>
:root{
  --blue:#1a5fc8;
  --blue-dark:#0d2a55;
  --navy:#0f1a30;
  --orange:#fb780d;
  --ink:#2b2b2b;
  --grey:#555;
  --white:#fff;
  --card-line:rgba(255,255,255,.55);
}
*{box-sizing:border-box;margin:0;padding:0}
html,body{width:1200px;height:3432px;overflow:hidden}
body{font-family:"Open Sans",Arial,sans-serif;color:var(--ink);background:#fff;position:relative}

/* hero */
.hero{position:absolute;left:0;top:0;width:1200px;height:725px;
  background:linear-gradient(180deg,#6fa7db 0%,#a9cbe8 35%,#dbe6ee 52%,#cfc5b4 62%,#d9d0c2 100%)}
.hero-photo{position:absolute;left:0;top:0;width:100%;height:100%}
.logo{position:absolute;left:96px;top:52px;display:flex;align-items:center;gap:12px}
.logo-dot{width:22px;height:22px;border-radius:50%;background:var(--blue)}
.logo-name{font-family:"Montserrat",sans-serif;font-weight:700;font-size:24px;color:var(--blue);line-height:1.05}
.topbar{position:absolute;top:26px;right:80px;display:flex;gap:40px;font-family:"Montserrat",sans-serif;font-weight:600;font-size:15px;color:var(--navy)}
.topbar span{display:flex;align-items:center;gap:8px}
.nav{position:absolute;top:74px;left:336px;display:flex;gap:33px;font-family:"Montserrat",sans-serif;font-weight:600;font-size:15.5px;color:var(--blue)}
.nav a{color:inherit;text-decoration:none;position:relative}
.nav a.active::after{content:"";position:absolute;left:0;right:0;bottom:-6px;border-bottom:2px solid var(--blue-dark)}
.arrow{position:absolute;top:310px}
.hero-title{position:absolute;left:112px;top:262px;font-family:"Montserrat",sans-serif;font-weight:500;font-size:44px;line-height:55px;color:var(--navy)}
.hero-title span{color:var(--blue);display:block}
.hero-text{position:absolute;left:112px;top:377px;width:400px;font-size:15px;line-height:27px;color:#333}
.btn{position:absolute;left:118px;top:457px;width:169px;height:50px;border:2px solid var(--blue);display:flex;align-items:center;justify-content:center;font-family:"Montserrat",sans-serif;font-weight:700;font-size:15px;color:var(--blue)}

/* intro */
.intro{position:absolute;left:100px;top:800px;width:1000px;text-align:center}
.intro h2{font-family:"Montserrat",sans-serif;font-weight:500;font-size:21.5px;line-height:38px;color:#333}
.intro p{margin:16px auto 0;width:940px;font-size:20px;line-height:38px;color:var(--grey)}

.illus{position:absolute;left:170px;top:1075px;width:385px;height:340px;border-radius:50%;background:radial-gradient(circle,#c9d3f2 0%,#e8ecfa 60%,#fff 75%)}
.benefits{position:absolute;left:616px;top:1115px}
.benefits h3{font-family:"Montserrat",sans-serif;font-weight:700;font-size:26px;color:var(--blue)}
.benefits ul{list-style:none;margin-top:22px}
.benefits li{position:relative;padding-left:39px;font-size:17px;line-height:30px;margin-bottom:10px;width:470px;color:#333}
.benefits li::before{content:"";position:absolute;left:9px;top:9px;width:13px;height:13px;border-radius:50%;background:var(--blue)}
.benefits li::after{content:"";position:absolute;left:13px;top:13px;width:3px;height:3px;border-right:2px solid #fff;border-top:2px solid #fff;transform:rotate(45deg)}

/* who section */
.who{position:absolute;left:0;top:1502px;width:621px;height:558px;background:var(--orange);color:#fff;padding:84px 30px 0 95px}
.who h2{font-family:"Montserrat",sans-serif;font-weight:700;font-size:26px;line-height:35px}
.who p{font-size:15px;line-height:24px;margin-top:12px}
.who p.first{margin-top:26px}
.who-photo{position:absolute;left:621px;top:1502px;width:579px;height:558px;background:linear-gradient(135deg,#d8b48f 0%,#c0926a 45%,#3c3c42 70%,#e6e0da 100%)}

/* why section */
.why{position:absolute;left:0;top:2059px;width:1200px;height:952px;background:linear-gradient(135deg,#0f2a5a 0%,#123a7c 50%,#1760c4 100%)}
.why h2{position:absolute;left:0;width:100%;top:70px;text-align:center;font-family:"Montserrat",sans-serif;font-weight:700;font-size:26px;color:#fff}
.card{position:absolute;width:249px;height:233px;border:1.5px solid var(--card-line);color:#fff;text-align:center;padding:28px 8px 0}
.card.on{background:var(--blue);border-color:var(--blue)}
.card svg{width:56px;height:56px;display:block;margin:0 auto}
.card h4{font-family:"Montserrat",sans-serif;font-weight:700;font-size:14px;line-height:23px;margin-top:14px;white-space:nowrap}
.card p{font-size:12.5px;line-height:19px;margin:12px 8px 0}

/* footer */
.footer{position:absolute;left:0;top:3010px;width:1200px;height:422px;background:var(--navy);color:#fff}
.footer h5{position:absolute;top:76px;font-family:"Montserrat",sans-serif;font-weight:500;font-size:22px;padding-bottom:4px;border-bottom:1.5px solid #fff}
.footer ul{position:absolute;top:134px;list-style:none;font-size:15.5px;line-height:29.5px}
.social{position:absolute;left:829px;top:141px;display:flex;gap:6px}
.social span{width:42px;height:42px;border:2px solid #fff;border-radius:50%}
.rule{position:absolute;left:152px;right:152px;top:360px;border-top:1px solid rgba(255,255,255,.35)}
.copy{position:absolute;top:377px;width:100%;text-align:center;font-size:13.5px}
</style>
</head>
<body>

<header class="hero">
  <div class="hero-photo" role="img" aria-label="Photo of a man in a beach chair working on a laptop by the sea"></div>
  <div class="logo"><div class="logo-dot"></div><div class="logo-name">REMOTE<br>HARBOR</div></div>
  <div class="topbar">
    <span><svg width="22" height="22" viewBox="0 0 24 24" fill="none" stroke="#1a5fc8" stroke-width="2"><path d="M5 3h4l2 5-3 2a12 12 0 0 0 6 6l2-3 5 2v4a2 2 0 0 1-2 2A17 17 0 0 1 3 5a2 2 0 0 1 2-2z"/></svg>(555) 014 2290</span>
    <span><svg width="26" height="18" viewBox="0 0 26 18"><rect width="26" height="18" rx="2" fill="#1a5fc8"/><path d="M1 2l12 9 12-9" stroke="#fff" stroke-width="2" fill="none"/></svg>hello@remoteharbor.example</span>
  </div>
  <nav class="nav">
    <a class="active" href="#">Home</a><a href="#">About Us</a><a href="#">Services offered</a><a href="#">Pricing</a><a href="#">Testimonials</a><a href="#">FAQs</a><a href="#">Contact Us</a><a href="#">Blog</a>
  </nav>
  <svg class="arrow" style="left:34px" width="22" height="40" viewBox="0 0 22 40"><path d="M19 3L4 20l15 17" stroke="#1a5fc8" stroke-width="4" fill="none"/></svg>
  <svg class="arrow" style="left:1154px" width="22" height="40" viewBox="0 0 22 40"><path d="M3 3l15 17L3 37" stroke="#1a5fc8" stroke-width="4" fill="none"/></svg>
  <h1 class="hero-title">VIRTUAL EMPLOYEE<span>RECRUITMENT</span></h1>
  <p class="hero-text">Praesent sit amet est In dictum dolor eu dictum porttitor enim felis viverra mi</p>
  <a class="btn">LEARN MORE</a>
</header>

<section class="intro">
  <h2>Tired of being stuck in your 9-5 cubicle job? Exhausted from commuting to and from<br>the office? Want to spend more time with your family? We’ve got you covered.</h2>
  <p>RemoteHarbor is a virtual staffing company that helps freelancers and virtual assistants find their perfect work-from-home job. We have a pool of clients from all over the world who are all looking for talented virtual assistants.</p>
</section>

<div class="illus" role="img" aria-label="Illustration of a woman sitting cross-legged with a laptop and a light bulb"></div>
<section class="benefits">
  <h3>With RemoteHarbor, you get to:</h3>
  <ul>
    <li>Work from the comfort of your home</li>
    <li>Have a competitive and steady income</li>
    <li>Achieve work-life balance</li>
    <li>Learn new skills for free</li>
    <li>Work with a dedicated team who can provide you with HR, payroll, IT, and training assistance 24/7!</li>
  </ul>
</section>

<section class="who">
  <h2>WHO ARE OUR<br>VIRTUAL ASSISTANTS?</h2>
  <p class="first">We have VAs from all over the Philippines.</p>
  <p>Our VA pool is composed of highly dedicated people armed with the right set of skills clients are looking for in a virtual assistant. We hire VAs of varying work experience and skill levels, and we help our VAs improve their skills so that they can get the jobs and clients they want.</p>
  <p>RemoteHarbor accepts VAs in a variety of niches. Currently, our VAs belongs to one or more of the following groups: Administrative VAs, eCommerce VAs, and Specialist VAs.</p>
  <p>Are you ready to join the team? To start the application process, please click on the button below.</p>
</section>
<div class="who-photo" role="img" aria-label="Photo of a person on a video call with colleagues on a laptop"></div>

<section class="why">
  <h2>WHY WORK FOR REMOTEHARBOR?</h2>

  <div class="card" style="left:82px;top:147px">
    <svg viewBox="0 0 56 56" fill="none" stroke="#fff" stroke-width="2"><path d="M6 36h8l10 4h10l12-8-3-3-10 5H24"/><path d="M14 32h10l6 3"/><text x="24" y="20" fill="#fff" stroke="none" font-size="18" font-family="Arial">$</text></svg>
    <h4>COMPETITIVE PAY<br>RATES</h4>
    <p>We offer competitive rates based on your years of experience and skill proficiency.</p>
  </div>
  <div class="card on" style="left:345px;top:147px">
    <svg viewBox="0 0 56 56" fill="none" stroke="#fff" stroke-width="2"><circle cx="28" cy="28" r="20"/><circle cx="28" cy="28" r="13"/><path d="M28 20v8l5 4"/></svg>
    <h4>FLEXIBLE HOURS</h4>
    <p>Full-time or part-time? We’ll match you with a client whose staffing needs perfectly matches your availability!</p>
  </div>
  <div class="card" style="left:606px;top:147px">
    <svg viewBox="0 0 56 56" fill="none" stroke="#fff" stroke-width="2"><rect x="8" y="10" width="34" height="30" rx="2"/><path d="M8 18h34M16 6v8M34 6v8"/><circle cx="42" cy="42" r="9"/><path d="M42 37v5h4"/></svg>
    <h4>FLEXIBLE SCHEDULE</h4>
    <p>We have clients from different time zones all over the world. We’ll help you find the best fit for your schedule.</p>
  </div>
  <div class="card" style="left:870px;top:147px">
    <svg viewBox="0 0 56 56" fill="none" stroke="#fff" stroke-width="2"><rect x="8" y="16" width="40" height="28" rx="3"/><path d="M8 24h40"/><rect x="34" y="30" width="14" height="8"/></svg>
    <h4>WEEKLY PAYOUT<br>VIA PAYWISE</h4>
    <p>Your work is billed by the hour, and we will pay your client-verified hours each week.</p>
  </div>

  <div class="card" style="left:82px;top:397px">
    <svg viewBox="0 0 56 56" fill="none" stroke="#fff" stroke-width="2"><rect x="6" y="12" width="38" height="28" rx="2"/><path d="M18 46h14M25 40v6"/><circle cx="42" cy="14" r="8"/><rect x="12" y="24" width="14" height="9"/></svg>
    <h4>PAYWISE FEES COVERED</h4>
    <p>Here at RemoteHarbor, we shoulder the Paywise fees. We want you to get your hard-earned money in full!</p>
  </div>
  <div class="card" style="left:345px;top:397px">
    <svg viewBox="0 0 56 56" fill="none" stroke="#fff" stroke-width="2"><circle cx="28" cy="14" r="7"/><path d="M6 36l22-8 22 8-22 8z"/><path d="M16 40v6h24v-6M46 37v10"/></svg>
    <h4>FREE TRAINING &amp;<br>UPSKILLING</h4>
    <p>Our trainers have created training programs that will help you improve your skills for free.</p>
  </div>
  <div class="card" style="left:606px;top:397px">
    <svg viewBox="0 0 56 56" fill="none" stroke="#fff" stroke-width="2"><path d="M12 6h22l8 8v14M12 6v34"/><path d="M18 16h14M18 22h18"/><rect x="20" y="32" width="28" height="16"/><circle cx="34" cy="40" r="4"/></svg>
    <h4>NO PLACEMENT OR<br>PROCESSING FEE</h4>
    <p>We don’t ask for placement or processing fees. We’re happy to match you with clients for free.</p>
  </div>
  <div class="card" style="left:870px;top:397px">
    <svg viewBox="0 0 56 56" fill="none" stroke="#fff" stroke-width="2"><path d="M6 28L28 8l22 20"/><path d="M12 24v24h32V24"/><rect x="22" y="32" width="12" height="16"/><circle cx="28" cy="22" r="4"/></svg>
    <h4>WORK FROM HOME</h4>
    <p>We spare you the time, effort and expense of the daily commute. All the work we offer is home-based.</p>
  </div>

  <div class="card" style="left:205px;top:650px">
    <svg viewBox="0 0 56 56" fill="none" stroke="#fff" stroke-width="2"><rect x="14" y="6" width="28" height="44" rx="3"/><path d="M20 14h16M20 20h16M20 28h10M20 34h16M20 40h10"/></svg>
    <h4>PAYROLL PROCESSING</h4>
    <p>We want you to focus on doing your client’s tasks, so our Accounting Department will take care of the invoicing for you!</p>
  </div>
  <div class="card" style="left:468px;top:650px">
    <svg viewBox="0 0 56 56" fill="none" stroke="#fff" stroke-width="2"><path d="M28 6l3 6 6 1-4 4 1 6-6-3-6 3 1-6-4-4 6-1z"/><rect x="20" y="30" width="16" height="18"/><rect x="6" y="36" width="14" height="12"/><rect x="36" y="40" width="14" height="8"/></svg>
    <h4>VARIOUS POSITIONS<br>AVAILABLE</h4>
    <p>From eCommerce work to content writing, we have a wide range of positions available for you.</p>
  </div>
  <div class="card" style="left:730px;top:650px">
    <svg viewBox="0 0 56 56" fill="none" stroke="#fff" stroke-width="2"><rect x="8" y="12" width="40" height="32" rx="2"/><path d="M14 20h12M14 26h12M14 32h12M14 38h12"/><circle cx="38" cy="26" r="6"/><path d="M30 40a8 8 0 0 1 16 0"/></svg>
    <h4 style="font-size:13.5px">CONTINUOUS<br>RE-ASSIGNMENT TO CLIENTS</h4>
    <p>Feel secure that we’re always ready to match you with our steady roster of clients looking for VAs!</p>
  </div>
</section>

<footer class="footer">
  <h5 style="left:151px">CONTACT US</h5>
  <ul style="left:152px">
    <li>48 Sample Lane #4B</li><li>Austin TX 78701</li><li>(555) 014 2290</li><li>hello@remoteharbor.example</li>
  </ul>
  <h5 style="left:459px">COMPANY</h5>
  <ul style="left:460px">
    <li>Home</li><li>About Us</li><li>Services offered</li><li>Pricing</li><li>Testimonials</li>
  </ul>
  <ul style="left:654px"><li>FAQs</li><li>Contact Us</li><li>Blog</li></ul>
  <h5 style="left:828px">FOLLOW US</h5>
  <div class="social" aria-label="Social links"><span></span><span></span><span></span><span></span></div>
  <div class="rule"></div>
  <p class="copy">© 2020 RemoteHarbor | All Rights Reserved</p>
</footer>

</body>
</html>
```